I need a business card design for a new business based in South West Australia.
I specialize in residential window cleaning & general handyman maintenance.

Dale Marsh - 412 SILVER HAWK DETAILING
- Window Cleaning
- House Maintenance

```html
<!DOCTYPE html>
<html lang="en">
<head>
<meta charset="utf-8">
<title>Silver Hawk Detailing – Business Card</title>
<link href="https://fonts.googleapis.com/css2?family=Open+Sans:wght@400;500;600&display=swap" rel="stylesheet">
<style>
  :root {
    --page-bg: #e9e7e4;
    --card-black: #121212;
    --sky-blue: #3f73b0;
    --photo-light: #c9d6e4;
    --photo-mid: #8ea7c4;
    --photo-dark: #4a5a6c;
    --brand-yellow: #f7d400;
    --text-white: #ffffff;
  }
  html, body {
    margin: 0;
    padding: 0;
    width: 1189px;
    height: 1200px;
    overflow: hidden;
    background: var(--page-bg);
  }
  .canvas {
    position: relative;
    width: 1189px;
    height: 1200px;
  }
  .business-card {
    position: absolute;
    left: 44px;
    top: 286px;
    width: 1100px;
    height: 628px;
    border-radius: 46px;
    overflow: hidden;
    background: var(--card-black);
  }
  .business-card svg {
    display: block;
    width: 100%;
    height: 100%;
  }
  .card-text {
    font-family: "Open Sans", "Segoe UI", sans-serif;
  }
  .company-name {
    fill: var(--brand-yellow);
    font-size: 47px;
    font-weight: 500;
    letter-spacing: 0.5px;
  }
  .person-name {
    fill: var(--text-white);
    font-size: 50px;
    font-weight: 500;
  }
  .phone-number {
    fill: var(--text-white);
    font-size: 33px;
    font-weight: 400;
  }
  .service-item {
    fill: var(--text-white);
    font-size: 34px;
    font-weight: 400;
  }
  .sky-band { fill: var(--sky-blue); }
  .black-panel { fill: var(--card-black); }
  .service-mark { fill: var(--text-white); }
</style>
</head>
<body>
<main class="canvas">
  <section class="business-card">
    <svg viewBox="0 0 1122 640" xmlns="http://www.w3.org/2000/svg">
      <defs>
        <linearGradient id="photo-tones" x1="0" y1="0" x2="1" y2="0.6">
          <stop offset="0" stop-color="var(--photo-light)"/>
          <stop offset="0.45" stop-color="var(--photo-mid)"/>
          <stop offset="0.75" stop-color="var(--photo-dark)"/>
          <stop offset="1" stop-color="var(--sky-blue)"/>
        </linearGradient>
      </defs>

      <rect class="sky-band" x="0" y="0" width="1122" height="640"/>

      <path role="img" aria-label="Photo of a squeegee wiping soapy water from a window"
            fill="url(#photo-tones)"
            d="M0,0 H1122 V28 C980,40 800,60 545,80 L0,440 Z"/>

      <path class="black-panel" d="M0,462 Q720,370 1122,52 V640 H0 Z"/>

      <g class="card-text">
        <text class="company-name" x="1073" y="438" text-anchor="end">SILVER HAWK DETAILING</text>
        <text class="person-name" x="82" y="525">Dale Marsh</text>
        <text class="phone-number" x="82" y="584">0400 182 562</text>
        <text class="service-item" x="988" y="520" text-anchor="end">House Maintenance</text>
        <text class="service-item" x="988" y="580" text-anchor="end">Window Cleaning</text>
      </g>

      <circle class="service-mark" role="img" aria-label="Fleur-de-lis ornament" cx="1053" cy="510" r="13"/>
      <circle class="service-mark" role="img" aria-label="Fleur-de-lis ornament" cx="1053" cy="572" r="13"/>
    </svg>
  </section>
</main>
</body>
</html>
```